Dental office stationary (letterhead, envelopes), business cards, presentation folders

Nothing too dental outside of the logo. I will need all stationary, presentation folders, business cards. Would prefer to stay in the colors of the logo

Gordon Patel, DDS
Bright Haven Dental Implant Center
555-318-2790
info@brighthavendental.example
4817 NW Maple Crest Rd Unit B
Harborview, ST 00000

Also need appointment date and time
And cancellation policy
I want it to say “kindly ask for
A 48hr cancellation policy to avoid incurring a cancellation fee”

Industry/Entity Type

Dental

Colors
0054AA
0677BA
7BADD7
CADEEF
E8F1F8

Requirements
Must have
• Name of your office, name of doctor, address, phone number
Should not have
• Too much tooth/dental. Only the tooth in logo

```html
<!DOCTYPE html>
<html lang="en">
<head>
<meta charset="utf-8">
<title>Bright Haven Dental Implant Center – Business Card</title>
<link rel="stylesheet" href="https://fonts.googleapis.com/css2?family=Arimo:wght@400;700&family=Libre+Baskerville:wght@700&display=swap">
<style>
  :root {
    --bg: #3d3d3d;
    --card-white: #ffffff;
    --blue-deep: #0f74c4;
    --blue-mid: #1797d8;
    --teal: #1fb39a;
    --brand-blue: #1a9fd8;
    --card-dark: #2d2d2d;
    --text-light: #ffffff;
  }
  * { margin: 0; padding: 0; box-sizing: border-box; }
  html, body { width: 1200px; height: 803px; overflow: hidden; background: var(--bg); }
  .canvas {
    position: relative; width: 1200px; height: 803px;
    display: flex; align-items: center; justify-content: center; gap: 50px;
  }
  .card {
    width: 520px; height: 297px; border-radius: 18px; overflow: hidden;
    position: relative; box-shadow: 0 14px 30px rgba(0,0,0,.35);
  }
  /* front */
  .card-front { background: var(--card-white); display: flex; flex-direction: column; }
  .front-brand {
    height: 140px; display: flex; align-items: center; justify-content: center; gap: 10px;
  }
  .brand-dot { width: 14px; height: 14px; border-radius: 50%; background: var(--brand-blue); flex: none; }
  .brand-name {
    font-family: "Arimo", sans-serif; font-weight: 400; font-size: 25px;
    letter-spacing: .04em; color: var(--brand-blue); text-transform: uppercase; text-align: center; line-height: 1.15;
  }
  .brand-name small { display: block; font-size: 13px; letter-spacing: .28em; }
  .divider-line { height: 4px; background: var(--teal); }
  .front-info {
    flex: 1; display: flex; align-items: center; padding: 0 26px;
    background: linear-gradient(180deg, var(--blue-mid) 0%, var(--blue-deep) 100%);
    color: var(--text-light);
  }
  .doctor { flex: 1; text-align: right; padding-right: 20px; white-space: nowrap; }
  .doctor-name {
    font-family: "Libre Baskerville", serif; font-weight: 700; font-size: 19px;
    text-transform: uppercase; line-height: 1.1;
  }
  .doctor-title { font-family: "Arimo", sans-serif; font-size: 12px; margin-top: 2px; }
  .doctor-email { font-family: "Arimo", sans-serif; font-size: 12px; margin-top: 10px; }
  .info-rule { width: 1px; height: 80px; background: rgba(255,255,255,.6); flex: none; }
  .contact { flex: 1; padding-left: 20px; font-family: "Arimo", sans-serif; font-size: 12px; line-height: 1.5; white-space: nowrap; }
  .contact-row { display: flex; align-items: center; gap: 6px; }
  .contact-row svg { width: 11px; height: 11px; flex: none; }
  .address { margin-bottom: 4px; }
  /* back */
  .card-back {
    background: var(--card-dark); border: 1px solid rgba(255,255,255,.55);
    display: flex; align-items: center; justify-content: center; gap: 12px;
  }
  .card-back .brand-name { font-size: 30px; }
  .card-back .brand-name small { font-size: 15px; }
</style>
</head>
<body>
<main class="canvas">
  <section class="card card-front" aria-label="Business card front">
    <div class="front-brand">
      <span class="brand-dot"></span>
      <div class="brand-name">Bright Haven<small>Dental Implant Center</small></div>
    </div>
    <div class="divider-line"></div>
    <div class="front-info">
      <div class="doctor">
        <div class="doctor-name">Gordon Patel</div>
        <div class="doctor-title">DDS</div>
        <div class="doctor-email">info@brighthavendental.example</div>
      </div>
      <div class="info-rule"></div>
      <div class="contact">
        <div class="address">4817 NW Maple Crest Rd Unit B<br>Harborview, ST 00000</div>
        <div class="contact-row">
          <svg viewBox="0 0 24 24" aria-hidden="true"><path fill="#fff" d="M6.6 10.8a15 15 0 0 0 6.6 6.6l2.2-2.2a1 1 0 0 1 1-.25 11.4 11.4 0 0 0 3.6.57 1 1 0 0 1 1 1V20a1 1 0 0 1-1 1A17 17 0 0 1 3 4a1 1 0 0 1 1-1h3.5a1 1 0 0 1 1 1c0 1.25.2 2.45.57 3.57a1 1 0 0 1-.25 1z"/></svg>
          <span>555-318-2790</span>
        </div>
        <div class="contact-row">
          <svg viewBox="0 0 24 24" aria-hidden="true"><circle cx="12" cy="12" r="9" fill="none" stroke="#fff" stroke-width="2"/><path d="M3 12h18M12 3c3 3 3 15 0 18M12 3c-3 3-3 15 0 18" fill="none" stroke="#fff" stroke-width="1.6"/></svg>
          <span>www.brighthavendental.example</span>
        </div>
      </div>
    </div>
  </section>

  <section class="card card-back" aria-label="Business card back">
    <span class="brand-dot"></span>
    <div class="brand-name">Bright Haven<small>Dental Implant Center</small></div>
  </section>
</main>
</body>
</html>
```